Upstart Retirement Planning Firm needs help with business card design

Harborview Nest Advisors, LLC is looking for help with business card design. We give advice on investments, insurance, and other financial matters related to retirement. There are some required disclosures that we will provide but mostly we are looking for a professional, classy business card that reflects the theme we have chosen. We have a logo that is attached but we would like to add a phrase; "Turning Your Earned Income Into Retirement Income"

Doubled sided only so that we can add the required disclosures (needed for our industry) on the back of the card. We will provide the exact words for this in 1-2 days.

Target Market(s)

Retirees and Pre-retirees. Professionals 50+ years old

Industry/Entity Type

Financial Planning

Contact Information for Business Card

We currently have two people who will need separate cards so we'd like to have a template so that we can add names for new cards in the future.

For the first run, please show the following information.

Gregor Pelham, MBA, ChFC®, CLU®
Financial Advisor, Registered Representative
gpelham@harborviewnest.example
Phone: (555) 318-2946
Toll Free Fax: (800) 555-0193

Address is
2187 Meadowlark Ridge Rd.
Suite K418
Virginia Beach, VA 23999

Colors
3277b5

Requirements
Must have
• Logo, contact info, small phase to describe business (in description), required legal disclosures on back of the card as follows (in small font)
• Gregor Pelham is a registered representative of and offers securities through Brightmoor Capital Brokerage Corporation, Member FNQX. Brightmoor Capital Brokerage Corporation is a member of the Brightmoor Capital Alliance which is the marketing name for Brightmoor Holding Corporation and its affiliates.
Nice to have
• Rounded edges, raised letters
Should not have
• any colors that aren't in the logo (other than black for font)

```html
<!DOCTYPE html>
<html lang="en">
<head>
<meta charset="utf-8">
<title>Harborview Nest Advisors – Business Card</title>
<link rel="stylesheet" href="https://fonts.googleapis.com/css2?family=PT+Serif:wght@400;700&display=swap">
<style>
  :root {
    --bg: #e4e4e4;
    --card: #ffffff;
    --brand-blue: #3277b5;
    --deep-blue: #1f5fa6;
    --silver: #a9abae;
    --silver-light: #cfd0d2;
    --ink: #1c1c1c;
    --black-band: #222428;
  }
  * { box-sizing: border-box; margin: 0; padding: 0; }
  html, body { width: 1200px; height: 1200px; overflow: hidden; }
  body {
    background: var(--bg);
    font-family: "PT Serif", Georgia, serif;
    color: var(--ink);
    position: relative;
  }
  .card {
    position: absolute;
    left: 250px;
    width: 700px;
    height: 400px;
    background: var(--card);
    border-radius: 26px;
    overflow: hidden;
    box-shadow: 0 6px 18px rgba(0,0,0,0.18);
  }
  .card--front { top: 110px; }
  .card--back { top: 650px; }
  .card__bands { position: absolute; inset: 0; width: 100%; height: 100%; }

  .brand {
    position: absolute;
    display: flex;
    align-items: center;
    gap: 12px;
    color: var(--brand-blue);
    font-weight: 400;
    letter-spacing: 0.5px;
  }
  .brand__dot {
    width: 22px; height: 22px; border-radius: 50%;
    background: var(--brand-blue);
    flex: none;
  }
  .card--front .brand { left: 0; right: 0; top: 160px; justify-content: center; font-size: 30px; }
  .card--back .brand { left: 44px; top: 130px; font-size: 20px; width: 260px; line-height: 1.2; }

  .contact { position: absolute; left: 340px; top: 70px; }
  .contact__name { color: var(--brand-blue); font-size: 30px; font-weight: 400; }
  .contact__role { font-size: 13px; line-height: 1.35; margin-top: 6px; }
  .contact__list { list-style: none; margin-top: 30px; font-size: 17px; line-height: 1.4; }
  .contact__list li { display: flex; align-items: center; gap: 12px; }
  .contact__list svg { width: 15px; height: 15px; fill: var(--brand-blue); flex: none; }
  .contact__address { font-size: 17px; line-height: 1.4; margin-top: 4px; padding-left: 27px; }
</style>
</head>
<body>

<section class="card card--front" aria-label="Card front">
  <svg class="card__bands" viewBox="0 0 700 400" preserveAspectRatio="none" aria-hidden="true">
    <path d="M570 350 L700 290 L700 330 L600 360 Z" fill="var(--silver)"/>
    <path d="M0 388 L470 368 Q540 362 600 338 L700 318 L700 400 L0 400 Z" fill="var(--deep-blue)"/>
    <path d="M0 394 L480 380 Q560 372 620 352 L700 338 L700 344 L620 360 Q560 380 480 388 L0 400 Z" fill="var(--brand-blue)"/>
  </svg>
  <div class="brand"><span class="brand__dot"></span>Harborview Nest Advisors, LLC</div>
</section>

<section class="card card--back" aria-label="Card back">
  <svg class="card__bands" viewBox="0 0 700 400" preserveAspectRatio="none" aria-hidden="true">
    <path d="M440 400 Q560 330 700 262 L700 290 Q590 340 520 400 Z" fill="var(--silver-light)"/>
    <path d="M480 400 Q580 340 700 282 L700 310 Q610 350 540 400 Z" fill="var(--silver)"/>
    <path d="M520 400 Q610 345 700 305 L700 400 Z" fill="var(--deep-blue)"/>
    <path d="M0 400 L0 392 Q260 388 520 360 L560 400 Z" fill="var(--black-band)"/>
    <path d="M0 396 Q280 394 540 372 L560 384 Q300 400 0 400 Z" fill="var(--brand-blue)"/>
  </svg>

  <div class="brand"><span class="brand__dot"></span>Harborview Nest Advisors, LLC</div>

  <div class="contact">
    <h1 class="contact__name">Gregor Pelham</h1>
    <p class="contact__role">MBA, ChFC®, CLU®<br>Financial Advisor, Registered Representative</p>
    <ul class="contact__list">
      <li><svg viewBox="0 0 16 16"><path d="M3 1h3l1 4-2 1a9 9 0 0 0 5 5l1-2 4 1v3c0 1-1 2-2 2A13 13 0 0 1 1 3c0-1 1-2 2-2z"/></svg>(555) 318-2946</li>
      <li><svg viewBox="0 0 16 16"><path d="M4 1h8v4H4zM1 6h14v7h-3v2H4v-2H1zm4 5v3h6v-3z"/></svg>(800) 555-0193</li>
      <li><svg viewBox="0 0 16 16"><path d="M1 3h14v10H1zm1 1v1l6 4 6-4V4z"/></svg>www.harborviewnest.example</li>
      <li><svg viewBox="0 0 16 16"><path d="M8 1a7 7 0 1 0 0 14A7 7 0 0 0 8 1zm0 1.5c.8 0 1.8 1.8 2 4.5H6c.2-2.7 1.2-4.5 2-4.5zM2.6 9h2.4c.1 1.6.5 3 1 3.9A5.5 5.5 0 0 1 2.6 9zm8.4 0h2.4a5.5 5.5 0 0 1-3.4 3.9c.5-.9.9-2.3 1-3.9zM6 9h4c-.2 2.7-1.2 4.5-2 4.5S6.2 11.7 6 9z"/></svg>gpelham@harborviewnest.example</li>
    </ul>
    <p class="contact__address">2187 Meadowlark Ridge Rd. Suite K418<br>Virginia Beach, VA 23999</p>
  </div>
</section>

</body>
</html>
```